A multi-page brochure that explains our firm ,KVL Wealth Management

We have a current brochure attached but it is a compilation of several items combined into one. We would like this to have the same content but be one complete theme. We are a financial planning form so it needs to have a level of professionalism but also a comfortable approach for clients and showing that was have a lot of resources and experience. We cater mostly to the 55-60+ age community.

We need the front page picture changed. lake themed would be great, like our website www.TheMoskaHouse.com
Just to be clear we use KVL Wealth Management now as our company name. Parent company name is The Moska House LLC. I attached the current mock brochure and our new logos.
Our logo colors are:
KVL WM Logo Colors:

Blue:
HEX: #0f75bc
RGB: rgba(15,117,188,255)

Grey:
HEX: #6d6e71
RGB: rgba(109,110,113,255)

Target Market(s)

High-level individuals that are looking for financial guidance who are 40 years old and up

Industry/Entity Type

Wealth Management

Requirements
Must have
• Clean and crisp
Nice to have
• https://www.bramblestoneplanners.com/wealth-management-brochure , this is a sample we like

```html
<!DOCTYPE html>
<html lang="en">
<head>
<meta charset="utf-8">
<title>KVL Wealth Management – Brochure Covers</title>
<link rel="stylesheet" href="https://fonts.googleapis.com/css2?family=Poppins:wght@700&family=Work+Sans:wght@400;500;600;700&display=swap">
<style>
  :root {
    --brand-blue: #0f75bc;
    --brand-grey: #6d6e71;
    --board-grey: #7a7a7a;
    --paper: #ffffff;
    --ink: #2b2b2b;
    --rule: #9aa9b8;
  }
  * { box-sizing: border-box; margin: 0; padding: 0; }
  html, body {
    width: 941px; height: 1200px; overflow: hidden;
    background: var(--board-grey);
    font-family: "Work Sans", Arial, sans-serif;
  }
  .board { position: relative; width: 941px; height: 1200px; }

  .option-label {
    position: absolute; top: 44px; width: 200px; text-align: center;
    font-family: "Poppins", Arial, sans-serif; font-weight: 700;
    font-size: 15px; color: #fff; letter-spacing: .3px;
  }
  .option-label--one { left: 149px; }
  .option-label--two { left: 592px; }

  .page {
    position: absolute; width: 395px; height: 511px;
    background: var(--paper); overflow: hidden;
  }
  .page--cover-one { left: 67px; top: 84px; }
  .page--cover-two { left: 495px; top: 84px; }
  .page--specialist { left: 67px; top: 627px; }
  .page--firm { left: 495px; top: 627px; }

  .wordmark {
    position: absolute; left: 0; width: 100%; text-align: center;
    color: var(--brand-blue); font-weight: 500; letter-spacing: .2px;
  }
  .page--cover-one .wordmark { top: 64px; font-size: 22px; }
  .page--cover-two .wordmark { top: 56px; font-size: 17px; }

  /* Cover one */
  .lake-photo--full {
    position: absolute; inset: 0;
    background: linear-gradient(180deg, #d5ebf7 0%, #a9d4ef 22%, #86bfe0 38%, #6fa9a8 50%, #3e97a6 62%, #5aa7ad 74%, #a39478 86%, #7e6d57 100%);
  }
  .title-panel {
    position: absolute; left: 102px; top: 158px; width: 190px; height: 195px;
    border: 1.5px solid rgba(255,255,255,.95);
  }
  .title-panel__fill {
    position: absolute; left: 6px; top: 6px; right: 6px; bottom: 6px;
    background: rgba(255,255,255,.78);
  }
  .title-panel__text {
    position: absolute; left: 0; right: 0; top: 28px; text-align: center;
    font-size: 23px; line-height: 29px; font-weight: 600;
  }
  .title-panel__muted { color: var(--brand-grey); display: block; }
  .title-panel__accent { color: var(--brand-blue); display: block; }

  /* Cover two */
  .cover-hero { position: absolute; left: 0; top: 0; }
  .cover-headline {
    position: absolute; left: 28px; top: 328px; width: 360px;
    color: var(--brand-blue); font-weight: 700; font-size: 26px; line-height: 36px;
  }
  .cover-url {
    position: absolute; left: 28px; top: 464px;
    display: flex; align-items: center; gap: 8px;
    color: var(--brand-grey); font-size: 15.5px; letter-spacing: .3px;
  }

  /* Inner pages */
  .office-photo {
    position: absolute; left: 0; top: 0; width: 395px; height: 239px;
    background: linear-gradient(160deg, #e3ecef 0%, #c9d6db 30%, #a8b1a8 55%, #8b7a66 75%, #5a4c40 100%);
  }
  .section-title {
    position: absolute; left: 28px;
    color: var(--brand-blue); font-weight: 500; font-size: 15px; letter-spacing: .6px;
  }
  .page--specialist .section-title { top: 287px; }
  .page--firm .section-title { top: 26px; }
  .body-copy {
    position: absolute; left: 28px; font-size: 7.2px; line-height: 9.1px; color: var(--ink);
  }
  .specialist-copy { top: 322px; width: 336px; }
  .specialist-copy p + p { margin-top: 9px; }
  .firm-intro { top: 61px; width: 340px; }

  .principles-band {
    position: absolute; left: 0; top: 105px; width: 395px; height: 200px;
    background: var(--brand-blue); color: #fff;
  }
  .principle { position: absolute; left: 28px; width: 165px; }
  .principle__icon { position: absolute; left: 0; top: 1px; }
  .principle__name { margin-left: 27px; font-weight: 700; font-size: 7.2px; line-height: 9px; }
  .principle__text { margin-left: 27px; font-size: 7.2px; line-height: 9.1px; margin-top: 2px; }
  .principle--service { top: 15px; }
  .principle--planning { top: 67px; }
  .principle--integrity { top: 137px; }

  .building-photo {
    position: absolute; left: 206px; top: 16px; width: 159px; height: 156px;
    background: linear-gradient(160deg, #1f7fd0 0%, #5aa6e6 40%, #dfe9f0 70%, #9fb58a 100%);
  }
  .photo-caption {
    position: absolute; left: 206px; width: 159px; text-align: center;
    font-weight: 700; font-size: 7.2px;
  }
  .principles-band .photo-caption { top: 180px; color: #fff; }
  .firm-detail { top: 328px; width: 162px; }
  .campus-photo {
    position: absolute; left: 206px; top: 328px; width: 159px; height: 65px;
    background: linear-gradient(180deg, #d6e6f2 0%, #b9cfe0 30%, #9b5a44 50%, #8a4e3c 68%, #6f9a4d 85%, #5c8a3f 100%);
  }
  .campus-caption { top: 400px; color: var(--brand-blue); }
  .disclaimer { top: 431px; width: 330px; }

  .page-footer {
    position: absolute; left: 28px; top: 473px; width: 337px; height: 9px;
    display: flex; align-items: center;
  }
  .page-footer__brand {
    background: var(--brand-blue); color: #fff; font-size: 5.4px;
    padding: 1px 3px; white-space: nowrap; line-height: 7px;
  }
  .page-footer__rule { flex: 1; height: 1px; background: var(--rule); }
  .page-footer__number {
    background: var(--brand-blue); color: #fff; font-size: 5.4px;
    padding: 1px 2px; line-height: 7px;
  }
</style>
</head>
<body>
<main class="board">
  <div class="option-label option-label--one">COVER 1</div>
  <div class="option-label option-label--two">COVER 2</div>

  <section class="page page--cover-one">
    <div class="lake-photo--full" role="img" aria-label="Lake scene with mountains, a wooden pier and rocky shoreline under a bright sky"></div>
    <div class="wordmark">KVL Wealth Management</div>
    <div class="title-panel">
      <div class="title-panel__fill"></div>
      <h1 class="title-panel__text">
        <span class="title-panel__muted">Wealth<br>Management</span>
        <span class="title-panel__accent">Focused on<br>Your Needs<br>and Vision</span>
      </h1>
    </div>
  </section>

  <section class="page page--cover-two">
    <svg class="cover-hero" width="395" height="330" viewBox="0 0 395 330">
      <defs>
        <linearGradient id="lakeTones" x1="0" y1="0" x2="0" y2="1">
          <stop offset="0" stop-color="#d5ebf7"/>
          <stop offset=".3" stop-color="#9fcdeb"/>
          <stop offset=".5" stop-color="#6fa79a"/>
          <stop offset=".68" stop-color="#3f98a8"/>
          <stop offset=".85" stop-color="#6ea7a0"/>
          <stop offset="1" stop-color="#9a8a70"/>
        </linearGradient>
      </defs>
      <rect width="395" height="310" fill="url(#lakeTones)" role="img" aria-label="Lake scene with cypress trees, a wooden pier and rocks in clear water"/>
      <path d="M0,282 C70,248 140,255 200,280 C270,308 340,290 395,244 L395,258 C340,300 270,318 200,288 C140,262 70,252 0,282Z" fill="#6d6e71"/>
      <path d="M0,284 C70,252 140,262 200,288 C270,318 340,300 395,258 L395,330 L0,330Z" fill="#ffffff"/>
    </svg>
    <div class="wordmark">KVL Wealth Management</div>
    <h1 class="cover-headline">Wealth Management Focused On Your Needs And Vision</h1>
    <div class="cover-url">
      <svg width="12" height="12" viewBox="0 0 12 12" aria-hidden="true">
        <circle cx="6" cy="6" r="5.2" fill="none" stroke="#0f75bc" stroke-width="1.3"/>
        <ellipse cx="6" cy="6" rx="2.2" ry="5.2" fill="none" stroke="#0f75bc" stroke-width="1"/>
        <line x1="1" y1="6" x2="11" y2="6" stroke="#0f75bc" stroke-width="1"/>
        <line x1="1.8" y1="3.5" x2="10.2" y2="3.5" stroke="#0f75bc" stroke-width=".8"/>
        <line x1="1.8" y1="8.5" x2="10.2" y2="8.5" stroke="#0f75bc" stroke-width=".8"/>
      </svg>
      <span>www.themoskahouse.com</span>
    </div>
  </section>

  <section class="page page--specialist">
    <div class="office-photo" role="img" aria-label="Advisor and client reviewing documents at a table in a bright office"></div>
    <h2 class="section-title">PARTNER WITH A SPECIALIST</h2>
    <div class="body-copy specialist-copy">
      <p>Understanding your unique needs and vision for the future is the starting point for our relationship. Together, we’ll assess where you are financially and where you want to be. Next, we’ll create a comprehensive wealth management plan that addresses your immediate and long-term goals. What about the unpredictable? We’ll plan for the changes that may be ahead, too.</p>
      <p>Exploring the topics of interest presented in this brochure will give you an idea of the depth and breadth of our services. Rest assured that we’ll partner with you throughout the planning process, always circling back to this fundamental question: what’s right for you and your loved ones?</p>
    </div>
    <div class="page-footer">
      <span class="page-footer__brand">KVL Wealth Management</span>
      <span class="page-footer__rule"></span>
      <span class="page-footer__number">02</span>
    </div>
  </section>

  <section class="page page--firm">
    <h2 class="section-title">OUR FIRM</h2>
    <p class="body-copy firm-intro">The Moska House LLC, established in 1987, is an independent, full-service, financial consulting firm. As we search the marketplace for innovative, strategic solutions, The Moska House is guided by the following principles:</p>

    <div class="principles-band">
      <div class="principle principle--service">
        <svg class="principle__icon" width="22" height="22" viewBox="0 0 22 22" aria-hidden="true">
          <circle cx="11" cy="11" r="10" fill="none" stroke="#fff" stroke-width="1"/>
          <circle cx="11" cy="9" r="3" fill="none" stroke="#fff" stroke-width="1"/>
          <path d="M6,16 C7,13 15,13 16,16" fill="none" stroke="#fff" stroke-width="1"/>
        </svg>
        <div class="principle__name">Service</div>
        <div class="principle__text">We seek to anticipate your needs and exceed your expectations in every aspect of our partnership.</div>
      </div>
      <div class="principle principle--planning">
        <svg class="principle__icon" width="22" height="22" viewBox="0 0 22 22" aria-hidden="true">
          <circle cx="11" cy="11" r="10" fill="none" stroke="#fff" stroke-width="1"/>
          <rect x="7" y="6" width="8" height="10" fill="none" stroke="#fff" stroke-width="1"/>
          <path d="M8.5,10 L10,11.5 L13,8.5" fill="none" stroke="#fff" stroke-width="1"/>
          <line x1="8.5" y1="13.5" x2="13.5" y2="13.5" stroke="#fff" stroke-width="1"/>
        </svg>
        <div class="principle__name">Planning</div>
        <div class="principle__text">We collaborate with you by listening, asking questions, educating and helping you make informed decisions to skillfully implement appropriate, effective financial strategies.</div>
      </div>
      <div class="principle principle--integrity">
        <svg class="principle__icon" width="22" height="22" viewBox="0 0 22 22" aria-hidden="true">
          <circle cx="11" cy="11" r="10" fill="none" stroke="#fff" stroke-width="1"/>
          <circle cx="11" cy="10" r="3.5" fill="none" stroke="#fff" stroke-width="1"/>
          <path d="M9,13 L8,17 L11,15.5 L14,17 L13,13" fill="none" stroke="#fff" stroke-width="1"/>
        </svg>
        <div class="principle__name">Integrity</div>
        <div class="principle__text">We build long-term client relationships and are proud of the integrity and sensitivity we exhibit when working with all our clients.</div>
      </div>
      <div class="building-photo" role="img" aria-label="Modern glass office building against a blue sky"></div>
      <div class="photo-caption">San Francisco Location</div>
    </div>

    <p class="body-copy firm-detail">The Moska House has created an environment of objectivity and independence in which to provide independent guidance and access to the widest variety of fiscal tools to support your financial goals. Our work complements the services of your existing advisors, including CPAs and attorneys. The degree and sophistication of the plan varies according to your circumstances.</p>
    <div class="campus-photo" role="img" aria-label="Red brick office building with green lawn"></div>
    <div class="photo-caption campus-caption">Minneapolis Location</div>
    <p class="body-copy disclaimer">*The Moska House LLC does not provide specific tax or legal advice. Please consult your accountant and/or attorney regarding your specific situation.</p>

    <div class="page-footer">
      <span class="page-footer__brand">KVL Wealth Management</span>
      <span class="page-footer__rule"></span>
      <span class="page-footer__number">02</span>
    </div>
  </section>
</main>
</body>
</html>
```